Oil Field Service company needs professional business cards

Looking to clean up our current company business cards and look a little more professional. Brenwick Casing Services is a US based company that services the oil field. We deal with engineers, managers and oil rigs....................................................................................................................................................................................................................................................................................................................................................................................................

Target Market(s)

Oil and Gas professionals

Industry/Entity Type

Oil And Gas

Contact Information for Business Card

See attached photo as example

Font styles to use
Sans Serif

Colors
ec1f27

Requirements
Must have
• Company Logo, Name, Title, Cell, Office, Fax, Email.
• See attached photo
Nice to have
• External CRT, Internal CRT, Casing Crews, Torque Turn, Laydown Machine
Should not have
• Do not introduce any new pictures and keep it professional looking

```html
<!DOCTYPE html>
<html lang="en">
<head>
<meta charset="utf-8">
<title>Brenwick Casing Services – Business Card</title>
<link href="https://fonts.googleapis.com/css2?family=Oswald:wght@300;400&family=Roboto:wght@400;700;900&display=swap" rel="stylesheet">
<style>
  :root {
    --brand-red: #cf1f24;
    --brand-red-deep: #bd1a1f;
    --slate: #3d4c5a;
    --ink: #2b2b2b;
    --card-white: #f7f7f5;
    --backdrop: #e9e9e9;
  }
  * { box-sizing: border-box; margin: 0; padding: 0; }
  html, body {
    width: 1200px; height: 576px; overflow: hidden;
    background: var(--backdrop);
  }
  .canvas { position: relative; width: 1200px; height: 576px; }

  .card {
    position: absolute; top: 139px;
    width: 484px; height: 293px;
    border-radius: 8px;
    box-shadow: 0 2px 4px rgba(0,0,0,.18);
  }

  /* Front */
  .card--front {
    left: 82px;
    background: linear-gradient(180deg, var(--brand-red) 0%, var(--brand-red-deep) 100%);
    display: flex; flex-direction: column; align-items: center; justify-content: center;
    color: #fff;
  }
  .front-name {
    font-family: 'Roboto', sans-serif; font-weight: 900;
    font-size: 40px; letter-spacing: 1px; line-height: 1;
    text-transform: uppercase;
  }
  .front-tagline {
    margin-top: 12px;
    font-family: 'Roboto', sans-serif; font-weight: 700;
    font-size: 15px; letter-spacing: 2.4px; text-transform: uppercase;
  }

  /* Back */
  .card--back { left: 602px; background: var(--card-white); }

  .back-brand {
    position: absolute; left: 0; top: 62px; width: 244px;
    text-align: center; color: var(--slate);
    font-family: 'Roboto', sans-serif; font-weight: 900; text-transform: uppercase;
  }
  .back-brand__name { font-size: 30px; line-height: 1; letter-spacing: .5px; }
  .back-brand__tagline { margin-top: 10px; font-size: 11px; letter-spacing: 1.9px; }

  .service-list {
    position: absolute; left: 0; top: 154px; width: 244px;
    list-style: none; text-align: center;
    font-family: 'Roboto', sans-serif; font-weight: 700; font-size: 13px;
    color: var(--ink); line-height: 18px;
  }

  .divider {
    position: absolute; left: 244px; top: 41px;
    width: 1px; height: 208px; background: var(--brand-red);
  }

  .contact-name {
    position: absolute; left: 272px; top: 53px;
    font-family: 'Oswald', sans-serif; font-weight: 400;
    font-size: 22px; color: var(--brand-red); line-height: 1.2;
  }
  .contact-title {
    position: absolute; left: 272px; top: 81px;
    font-family: 'Roboto', sans-serif; font-size: 11.5px; color: #444;
  }

  .contact-list {
    position: absolute; left: 272px; top: 139px; list-style: none;
    font-family: 'Oswald', sans-serif; font-weight: 300; font-size: 12px;
    color: var(--ink);
  }
  .contact-list li { display: flex; align-items: center; height: 16px; }
  .contact-list svg { width: 9px; height: 9px; margin-right: 11px; fill: var(--brand-red); flex: none; }
</style>
</head>
<body>
<div class="canvas">

  <section class="card card--front">
    <div class="front-name">Brenwick</div>
    <div class="front-tagline">Casing Services</div>
  </section>

  <section class="card card--back">
    <div class="back-brand">
      <div class="back-brand__name">Brenwick</div>
      <div class="back-brand__tagline">Casing Services</div>
    </div>

    <ul class="service-list">
      <li>Laydown Machine</li>
      <li>Casing Crew</li>
      <li>Mud Tool</li>
      <li>Torque Turn</li>
    </ul>

    <div class="divider"></div>

    <h1 class="contact-name">Colt Ramsey</h1>
    <p class="contact-title">Area Manager</p>

    <ul class="contact-list">
      <li>
        <svg viewBox="0 0 10 10" aria-hidden="true"><path d="M2 0.5 L3.6 2.6 L2.8 3.6 Q4 6 6.4 7.2 L7.4 6.4 L9.5 8 L8.4 9.6 Q1.5 8 0.4 1.6 Z"/></svg>
        (580) 555-0142
      </li>
      <li>
        <svg viewBox="0 0 10 10" aria-hidden="true"><path d="M0 3 Q5 -0.5 10 3 L10 4.2 L7.6 4.2 L7.4 3.2 L2.6 3.2 L2.4 4.2 L0 4.2 Z M1.5 5 L8.5 5 L9.5 9.5 L0.5 9.5 Z"/></svg>
        (580) 555-0187
      </li>
      <li>
        <svg viewBox="0 0 10 10" aria-hidden="true"><path d="M2.5 0.5 H7.5 V3 H2.5 Z M0.5 3.5 H9.5 V7.5 H8 V6 H2 V7.5 H0.5 Z M2.6 6.6 H7.4 V9.5 H2.6 Z"/></svg>
        (580) 555-0163
      </li>
      <li>
        <svg viewBox="0 0 10 10" aria-hidden="true"><path d="M5 0 A3.6 3.6 0 0 1 8.6 3.6 Q8.6 6 5 10 Q1.4 6 1.4 3.6 A3.6 3.6 0 0 1 5 0 Z M5 2.2 A1.4 1.4 0 1 0 5 5 A1.4 1.4 0 1 0 5 2.2 Z"/></svg>
        Harlan, OK 73850
      </li>
      <li>
        <svg viewBox="0 0 10 10" aria-hidden="true"><path d="M0 1.8 H10 V2.6 L5 5.8 L0 2.6 Z M0 3.8 L5 7 L10 3.8 V8.4 H0 Z"/></svg>
        coltramsey@brenwicksrvs.com
      </li>
      <li>
        <svg viewBox="0 0 10 10" aria-hidden="true"><path d="M5 0.2 A4.8 4.8 0 1 0 5 9.8 A4.8 4.8 0 1 0 5 0.2 Z M5 1.2 Q6.6 3 6.6 5 Q6.6 7 5 8.8 Q3.4 7 3.4 5 Q3.4 3 5 1.2 Z M1.2 4.6 H8.8 V5.4 H1.2 Z" fill-rule="evenodd"/></svg>
        www.brenwicksrvs.com
      </li>
    </ul>
  </section>

</div>
</body>
</html>
```